Harborline Benches business cards

I’d like a business card design that includes my logo, a tag line and my contact info. Black, textured background. My contact info color should match the orange and blue gradients. Tagline under logo: “Wooden Tables and Furniture of the Highest Quality”

Target Market(s)

High end furniture buyers

Contact Information for Business Card

Contact info, logo and tagline

```html
<!DOCTYPE html>
<html lang="en">
<head>
<meta charset="utf-8">
<title>Harborline Benches — Business Cards</title>
<link href="https://fonts.googleapis.com/css2?family=Poppins:wght@400;600;700&display=swap" rel="stylesheet">
<style>
  :root {
    --page-bg: #2a2a2c;
    --card-black: #0d0d0d;
    --card-black-edge: #151515;
    --card-slate: #1d232b;
    --card-slate-deep: #14181e;
    --orange: #f07a24;
    --orange-line: #c8651f;
    --blue: #2f7fd6;
    --blue-light: #4aa3ea;
    --text-light: #d9d9d9;
    --text-muted: #bdbdbd;
  }
  * { box-sizing: border-box; margin: 0; padding: 0; }
  html, body {
    width: 1200px; height: 900px; overflow: hidden;
    background: var(--page-bg);
    font-family: "Poppins", sans-serif;
  }
  .sheet {
    width: 1200px; height: 900px;
    display: flex; flex-direction: column; align-items: center; justify-content: center;
    gap: 36px;
  }
  .card {
    width: 700px; height: 400px;
    position: relative;
    border-radius: 4px;
    box-shadow: 0 14px 30px rgba(0,0,0,.45);
    overflow: hidden;
  }
  .card--front {
    background:
      repeating-linear-gradient(0deg, rgba(255,255,255,.012) 0 1px, transparent 1px 3px),
      radial-gradient(ellipse at 30% 30%, var(--card-black-edge), var(--card-black) 70%);
  }
  .card--back {
    background: linear-gradient(160deg, var(--card-slate) 0%, var(--card-slate-deep) 100%);
    display: flex; align-items: center; justify-content: center;
  }
  .brand {
    display: inline-flex; flex-direction: column; align-items: flex-start;
    color: var(--orange); font-weight: 600;
  }
  .brand__name { display: flex; align-items: center; gap: 10px; line-height: 1.15; }
  .brand__dot {
    width: 12px; height: 12px; border-radius: 50%;
    background: var(--orange); flex: none;
  }
  .brand__rule {
    height: 2px; width: 100%; margin-top: 6px;
    background: linear-gradient(90deg, var(--orange), var(--blue));
  }
  .card--front .brand {
    position: absolute; left: 44px; top: 176px;
    font-size: 26px;
  }
  .card--back .brand { font-size: 44px; }
  .card--back .brand__dot { width: 16px; height: 16px; }
  .card--back .brand__rule { height: 3px; margin-top: 10px; background: linear-gradient(90deg, var(--orange), var(--blue-light)); }
  .divider {
    position: absolute; left: 376px; top: 70px;
    width: 1px; height: 200px; background: var(--orange-line);
  }
  .contact {
    position: absolute; left: 404px; top: 78px;
    color: var(--text-light);
  }
  .contact__name {
    color: var(--orange); font-weight: 700; font-size: 22px;
    letter-spacing: .5px; text-transform: uppercase; line-height: 1.1;
  }
  .contact__role { font-size: 15px; color: var(--text-muted); margin-bottom: 14px; }
  .contact__list { list-style: none; font-size: 14px; line-height: 1.7; }
  .contact__list li { display: flex; align-items: center; gap: 10px; }
  .contact__list svg { width: 14px; height: 14px; flex: none; }
  .contact__address { margin-top: 12px; font-size: 14px; line-height: 1.45; padding-left: 24px; }
  .tagline {
    position: absolute; left: 0; right: 0; bottom: 48px;
    text-align: center;
    color: var(--orange); font-weight: 700; font-size: 19px;
    text-transform: uppercase; letter-spacing: .3px;
  }
</style>
</head>
<body>
<main class="sheet">
  <section class="card card--front" aria-label="Business card front">
    <div class="brand">
      <span class="brand__name"><span class="brand__dot"></span><span>Harborline Benches</span></span>
      <span class="brand__rule"></span>
    </div>
    <div class="divider"></div>
    <div class="contact">
      <p class="contact__name">Marcus Delaney</p>
      <p class="contact__role">Managing Director</p>
      <ul class="contact__list">
        <li>
          <svg viewBox="0 0 24 24" aria-hidden="true"><path fill="var(--orange)" d="M6.6 10.8a15.1 15.1 0 0 0 6.6 6.6l2.2-2.2a1 1 0 0 1 1-.25 11.4 11.4 0 0 0 3.6.57 1 1 0 0 1 1 1V20a1 1 0 0 1-1 1A17 17 0 0 1 3 4a1 1 0 0 1 1-1h3.5a1 1 0 0 1 1 1c0 1.25.2 2.45.57 3.57a1 1 0 0 1-.25 1z"/></svg>
          044-555 210 384
        </li>
        <li>
          <svg viewBox="0 0 24 24" aria-hidden="true"><path fill="var(--orange)" d="M2 5h20v14H2z"/><path fill="none" stroke="var(--card-black)" stroke-width="2" d="M2 5l10 8 10-8"/></svg>
          hello@harborlinebenches.com
        </li>
        <li>
          <svg viewBox="0 0 24 24" aria-hidden="true"><g fill="none" stroke="var(--orange)" stroke-width="2"><circle cx="12" cy="12" r="10"/><path d="M2 12h20M12 2c3 3 3 17 0 20M12 2c-3 3-3 17 0 20"/></g></svg>
          www.harborlinebenches.com
        </li>
      </ul>
      <p class="contact__address">88 Quayside Lane, Harbor Row<br>38160, Portmere</p>
    </div>
    <p class="tagline">Wooden Tables and Furniture of the Highest Quality</p>
  </section>

  <section class="card card--back" aria-label="Business card back">
    <div class="brand">
      <span class="brand__name"><span class="brand__dot"></span><span>Harborline Benches</span></span>
      <span class="brand__rule"></span>
    </div>
  </section>
</main>
</body>
</html>
```